Business Card Design Project - del varosi group

dear Sirs

we need business card design for our group ( DEL Varosi Group ) , i have got the Logo design of our group from pixel harbor in previous , so all need details relating to our group i think available with you, as well as the the chosen logo design

we hope to provide us with business card logo that to be appropaite and satisfactory to us .

thanks

note : logo design of our group is attached .
Updates

Reason: please extend the deadline of my project for additional 15 days because i didn't received appropriate design for our gruop yet . kindly beaware that i have received 77 design till now , supossed to send me 200-250 design at least . thanks

Target Market(s)

contents

name : Kerem EL Nadiri

position : Operation Manager

Industry/Entity Type

Business

Requirements
Must have

• person name

group logo
Nice to have
• logo color matching with back background

```html
<!DOCTYPE html>
<html lang="en">
<head>
<meta charset="utf-8">
<title>DEL Varosi Group – Business Card</title>
<link href="https://fonts.googleapis.com/css2?family=Open+Sans:wght@400;600;700&display=swap" rel="stylesheet">
<style>
  :root {
    --backdrop: #b8891f;
    --blue-deep: #0d4c8c;
    --blue-mid: #1a6aae;
    --blue-light: #3a8fd0;
    --gold: #c99a32;
    --gold-light: #f1dc9c;
    --white: #ffffff;
    --text-blue: #1a5fa6;
  }
  * { margin: 0; padding: 0; box-sizing: border-box; }
  html, body { width: 1200px; height: 686px; overflow: hidden; }
  body {
    background: var(--backdrop);
    font-family: "Open Sans", Arial, sans-serif;
    position: relative;
  }
  .card {
    position: absolute;
    width: 490px;
    height: 279px;
    border-radius: 26px;
    overflow: hidden;
    box-shadow: 0 3px 8px rgba(0,0,0,0.35);
  }
  /* Front */
  .card-front { left: 89px; top: 100px; background: var(--white); }
  .brand {
    position: absolute;
    left: 0; right: 0;
    display: flex;
    align-items: center;
    justify-content: center;
    gap: 12px;
    font-weight: 700;
    letter-spacing: 0.5px;
  }
  .brand-mark { width: 22px; height: 22px; }
  .card-front .brand { top: 70px; font-size: 34px; color: var(--blue-deep); }
  .card-front .brand-mark { background: var(--gold); }
  .holder {
    position: absolute;
    top: 164px; left: 0; right: 0;
    text-align: center;
    font-size: 14.5px;
  }
  .holder-name { color: var(--text-blue); font-weight: 700; }
  .holder-divider { color: #333; margin: 0 6px; font-weight: 400; }
  .holder-role { color: var(--gold); font-weight: 700; font-size: 12.5px; }
  .front-rule {
    position: absolute; top: 201px; left: 0; right: 0;
    height: 3px; background: var(--gold);
  }
  .contact-band {
    position: absolute; top: 205px; left: 0; right: 0; bottom: 0;
    background: radial-gradient(ellipse at 50% 40%, var(--blue-light), var(--blue-mid) 45%, var(--blue-deep));
    color: var(--white);
    font-size: 12px;
    text-align: center;
    padding-top: 13px;
    line-height: 18px;
  }
  .contact-row { display: flex; justify-content: center; gap: 14px; }
  .contact-item { display: inline-flex; align-items: center; gap: 3px; }
  .contact-item svg { width: 11px; height: 11px; fill: var(--white); }
  .contact-address { margin-top: 3px; }
  /* Back */
  .card-back {
    left: 611px; top: 318px;
    background: radial-gradient(ellipse at 50% 40%, var(--blue-light), var(--blue-mid) 50%, var(--blue-deep));
  }
  .card-back .brand { top: 100px; font-size: 38px; color: var(--white); }
  .card-back .brand-mark { background: var(--white); }
  .back-rule {
    position: absolute; top: 242px; left: 0; right: 0;
    height: 4px; background: var(--gold);
  }
  .back-footer {
    position: absolute; top: 249px; left: 0; right: 0; bottom: 0;
    background: linear-gradient(90deg, var(--gold), var(--gold-light) 50%, var(--gold));
    color: var(--white);
    font-size: 12px;
    font-weight: 700;
    letter-spacing: 1.5px;
    text-align: center;
    line-height: 30px;
  }
</style>
</head>
<body>

<section class="card card-front">
  <div class="brand"><span class="brand-mark"></span>DEL Varosi Group</div>
  <p class="holder">
    <span class="holder-name">Kerem EL Nadiri</span><span class="holder-divider">|</span><span class="holder-role">Operation Manager</span>
  </p>
  <div class="front-rule"></div>
  <div class="contact-band">
    <div class="contact-row">
      <span class="contact-item"><svg viewBox="0 0 24 24"><path d="M6.6 10.8a15 15 0 0 0 6.6 6.6l2.2-2.2a1 1 0 0 1 1-.25 11 11 0 0 0 3.6.6 1 1 0 0 1 1 1V20a1 1 0 0 1-1 1A17 17 0 0 1 3 4a1 1 0 0 1 1-1h3.5a1 1 0 0 1 1 1 11 11 0 0 0 .6 3.6 1 1 0 0 1-.25 1z"/></svg>(TF)123-456-7890</span>
      <span class="contact-item"><svg viewBox="0 0 24 24"><path d="M6.6 10.8a15 15 0 0 0 6.6 6.6l2.2-2.2a1 1 0 0 1 1-.25 11 11 0 0 0 3.6.6 1 1 0 0 1 1 1V20a1 1 0 0 1-1 1A17 17 0 0 1 3 4a1 1 0 0 1 1-1h3.5a1 1 0 0 1 1 1 11 11 0 0 0 .6 3.6 1 1 0 0 1-.25 1z"/></svg>123-456-7890</span>
      <span class="contact-item"><svg viewBox="0 0 24 24"><path d="M6 2h10v6H6zM3 9h18v10H3zM6 15h12v7H6z"/></svg>123-456-7890</span>
    </div>
    <div class="contact-row">
      <span class="contact-item"><svg viewBox="0 0 24 24"><path d="M2 5h20v14H2zM2 5l10 8 10-8" stroke="#0d4c8c" stroke-width="1.5"/></svg>name@website.com</span>
      <span class="contact-item"><svg viewBox="0 0 24 24"><circle cx="12" cy="12" r="10"/><path d="M2 12h20M12 2c3 3 3 17 0 20M12 2c-3 3-3 17 0 20" stroke="#0d4c8c" stroke-width="1.5" fill="none"/></svg>www.website.com</span>
    </div>
    <div class="contact-address">Street name City, State, zip code</div>
  </div>
</section>

<section class="card card-back">
  <div class="brand"><span class="brand-mark"></span>DEL Varosi Group</div>
  <div class="back-rule"></div>
  <div class="back-footer">www.website.com</div>
</section>

</body>
</html>
```